Specialized Personal Trainer Needs a Business Card Design

I need a business card design for my personal training business called Tall Oak Fitness. I have my Human Kinetics degree in Exercise Science from the Halvering Polytechnic Institute as well as an extra certification from NFBP (National Federation of Body Practice). I work as a Cardiac Rehab Exercise Specialist and personal trainer giving specialized exercise prescriptions to those that have different heart conditions as well as work with the general population in weight loss, strength and conditioning, getting/staying fit.
Updates

I decided that I wanted a logo (as I did not have one before I submitted my project for a business card) so I am submitting a project to get a logo done and then I will decide on a business card, hopefully being able to use one of the designs already submitted.  My apologies for doing this backwards.  I am new to this so I appreciate your patience.

Thank you.

Hi, I have just created a project for a logo design (I realized I needed a logo and I should've done that first..oops!), please feel free to participate.  Once I receive a logo I like I will finalize my business card project and hopefully incorporate it into one of your business card designs. 

Thank you!

Target Market(s)

Business professionals

Industry/Entity Type

Personal Trainer

Requirements
Must have
• My name with my info:
Delphine R. Ashcroft (BHK)
NFBP Certified Clinical Exercise Specialist & Personal Trainer
del.ashcroft@talloakfitness.example
Cell: 555-302-6148

Please make it double sided.
Nice to have
• An image that represents cardiac and general fitness training.

```html
<!DOCTYPE html>
<html lang="en">
<head>
<meta charset="utf-8">
<title>Tall Oak Fitness – Business Card</title>
<link rel="stylesheet" href="https://fonts.googleapis.com/css2?family=Barlow:wght@400&family=Barlow+Condensed:wght@800&family=Roboto+Condensed:wght@400;600&display=swap">
<style>
  :root {
    --brand-red: #e41b36;
    --paper: #ffffff;
    --page: #ffffff;
    --edge: #d9d9d9;
    --shadow: rgba(0, 0, 0, 0.28);
  }
  * { margin: 0; padding: 0; box-sizing: border-box; }
  html, body {
    width: 1200px;
    height: 901px;
    overflow: hidden;
    background: var(--page);
  }
  .canvas {
    position: relative;
    width: 1200px;
    height: 901px;
  }
  .card {
    position: absolute;
    left: 267px;
    width: 675px;
    height: 385px;
    border-radius: 36px;
    box-shadow: 0 6px 8px var(--shadow);
    overflow: hidden;
  }
  .card--front {
    top: 43px;
    background: var(--brand-red);
    display: flex;
    align-items: center;
    justify-content: center;
  }
  .wordmark {
    font-family: "Barlow Condensed", "Arial Narrow", sans-serif;
    font-weight: 800;
    color: var(--paper);
    font-size: 70px;
    line-height: 0.98;
    text-align: center;
    letter-spacing: 1px;
    text-transform: uppercase;
  }
  .card--back {
    top: 467px;
    background: var(--paper);
    border: 1.5px solid var(--edge);
    color: var(--brand-red);
  }
  .services {
    position: absolute;
    top: 48px;
    left: 0;
    width: 100%;
    text-align: center;
    font-family: "Barlow", Arial, sans-serif;
    font-size: 18px;
    letter-spacing: 1.2px;
    text-transform: uppercase;
    word-spacing: 2px;
  }
  .services .divider { margin: 0 14px; }
  .identity {
    position: absolute;
    top: 134px;
    left: 0;
    width: 100%;
    text-align: center;
    font-family: "Roboto Condensed", "Arial Narrow", sans-serif;
  }
  .identity__business {
    font-weight: 600;
    font-size: 38px;
    line-height: 1.1;
  }
  .identity__name {
    font-weight: 600;
    font-size: 28px;
    margin-top: 12px;
    line-height: 1.1;
  }
  .identity__degree {
    font-weight: 400;
    font-size: 21px;
  }
  .identity__credential {
    font-weight: 400;
    font-size: 20px;
    margin-top: 3px;
  }
  .contact {
    position: absolute;
    left: 29px;
    top: 280px;
    font-family: "Roboto Condensed", "Arial Narrow", sans-serif;
    font-size: 23px;
    line-height: 27px;
    list-style: none;
  }
</style>
</head>
<body>
  <main class="canvas">
    <section class="card card--front" aria-label="Card front">
      <h1 class="wordmark">Tall Oak<br>Fitness</h1>
    </section>

    <section class="card card--back" aria-label="Card back">
      <p class="services">
        Training<span class="divider">|</span>Cardiac Rehabilitation<span class="divider">|</span>Wellness
      </p>
      <div class="identity">
        <h2 class="identity__business">Tall Oak Fitness</h2>
        <p class="identity__name">Delphine R. Ashcroft <span class="identity__degree">(BHK)</span></p>
        <p class="identity__credential">NFBP Certified Clinical Exercise Specialist &amp; Personal Trainer</p>
      </div>
      <ul class="contact">
        <li class="contact__phone">555-302-6148</li>
        <li class="contact__web">www.talloakfitness.example</li>
        <li class="contact__email">del.ashcroft@talloakfitness.example</li>
      </ul>
    </section>
  </main>
</body>
</html>
```